Specialised investor in e-mobility and energy wants business card design

We need a business card design that fits our existing corporate design. <The look and feel must be 'sharp'/'clean', dynamic, communicate momentum, professionalism etc (as one would imagine from a firm in the financial sector). We like the idea of a reverse-side of the card that includes the logo, and the name and contact details on the other. We expect the deliverable to be whatever format might be required to be able to get cards printed directly by a service such as kelmo press. Our website is www.zub.capital

```html
<!DOCTYPE html>
<html lang="en">
<head>
<meta charset="utf-8">
<title>Zub Capital – Business Card</title>
<link href="https://fonts.googleapis.com/css2?family=Montserrat:wght@300;400;700&display=swap" rel="stylesheet">
<style>
  :root {
    --bg: #5a5a5c;
    --ink: #ffffff;
    --night-blue: #123a6b;
    --teal: #1f4f5a;
    --olive: #5b6a1e;
    --amber: #8a7a2a;
    --deep: #0e1f24;
  }
  * { margin: 0; padding: 0; box-sizing: border-box; }
  html, body { width: 1200px; height: 900px; overflow: hidden; }
  body {
    background: var(--bg);
    font-family: "Montserrat", sans-serif;
    color: var(--ink);
    display: flex;
    flex-direction: column;
    align-items: center;
    justify-content: center;
    gap: 34px;
  }
  .card {
    position: relative;
    width: 720px;
    height: 411px;
    overflow: hidden;
    box-shadow: 0 10px 28px rgba(0,0,0,.35);
  }
  .card__photo {
    position: absolute;
    inset: 0;
    background:
      radial-gradient(ellipse at 78% 18%, rgba(210,190,90,.45), transparent 40%),
      linear-gradient(125deg, var(--night-blue) 0%, var(--teal) 35%, var(--olive) 68%, var(--amber) 100%);
  }
  .card__photo::after {
    content: "";
    position: absolute;
    inset: 0;
    background: linear-gradient(to bottom, rgba(14,31,36,.45), transparent 45%, rgba(14,31,36,.25));
  }
  .brand {
    position: absolute;
    display: flex;
    align-items: center;
    gap: 14px;
    font-weight: 300;
    letter-spacing: .5px;
    white-space: nowrap;
  }
  .brand__dot {
    display: inline-block;
    border: 3px solid var(--ink);
    border-radius: 50%;
  }
  .card--front .brand { left: 50%; top: 50%; transform: translate(-50%, -50%); font-size: 82px; }
  .card--front .brand__dot { width: 54px; height: 54px; }
  .card--back .brand { right: 34px; top: 30px; font-size: 46px; }
  .card--back .brand__dot { width: 32px; height: 32px; border-width: 2px; }

  .contact {
    position: absolute;
    left: 40px;
    top: 96px;
    font-size: 14px;
    line-height: 20px;
  }
  .contact__name { font-weight: 700; font-size: 16px; letter-spacing: .5px; text-transform: uppercase; }
  .contact__role { margin-bottom: 8px; }
  .contact__line { display: flex; align-items: center; gap: 10px; }
  .contact__line svg { width: 14px; height: 14px; flex: none; }
  .contact__details { margin-bottom: 12px; }
  .team__member { margin-bottom: 10px; }

  .address {
    position: absolute;
    right: 34px;
    bottom: 120px;
    text-align: right;
    font-size: 15px;
    line-height: 22px;
    font-style: normal;
  }
</style>
</head>
<body>

<section class="card card--front">
  <div class="card__photo" role="img" aria-label="Night city street with skyscrapers and light trails of traffic, blue and olive tones"></div>
  <div class="brand"><span class="brand__dot"></span>zub capital</div>
</section>

<section class="card card--back">
  <div class="card__photo" role="img" aria-label="Night city street with skyscrapers and light trails of traffic, blue and olive tones"></div>
  <div class="brand"><span class="brand__dot"></span>zub capital</div>

  <div class="contact">
    <p class="contact__name">Peter Ashcombe</p>
    <p class="contact__role">team directly</p>
    <div class="contact__details">
      <p class="contact__line">
        <svg viewBox="0 0 16 16" fill="#fff"><path d="M3 1h3l1.5 4-2 1.2a9 9 0 0 0 4.3 4.3L11 8.5l4 1.5v3a2 2 0 0 1-2 2A12 12 0 0 1 1 3a2 2 0 0 1 2-2z"/></svg>
        +99 70000 4815
      </p>
      <p class="contact__line">
        <svg viewBox="0 0 16 16" fill="none" stroke="#fff" stroke-width="1.5"><rect x="1" y="3" width="14" height="10"/><path d="M1 3l7 6 7-6"/></svg>
        peter@zub.capital
      </p>
      <p class="contact__line">
        <svg viewBox="0 0 16 16" fill="none" stroke="#fff" stroke-width="1.3"><circle cx="8" cy="8" r="6.5"/><ellipse cx="8" cy="8" rx="3" ry="6.5"/><path d="M1.5 8h13"/></svg>
        www.zub.capital
      </p>
    </div>
    <div class="team">
      <div class="team__member">
        <p>Kenji Arakawa</p>
        <p class="contact__line"><svg viewBox="0 0 16 16" fill="none" stroke="#fff" stroke-width="1.5"><rect x="1" y="3" width="14" height="10"/><path d="M1 3l7 6 7-6"/></svg>kenji@zub.capital</p>
      </div>
      <div class="team__member">
        <p>Daniel Moreau</p>
        <p class="contact__line"><svg viewBox="0 0 16 16" fill="none" stroke="#fff" stroke-width="1.5"><rect x="1" y="3" width="14" height="10"/><path d="M1 3l7 6 7-6"/></svg>daniel@zub.capital</p>
      </div>
      <div class="team__member">
        <p>Laura Penrose</p>
        <p class="contact__line"><svg viewBox="0 0 16 16" fill="none" stroke="#fff" stroke-width="1.5"><rect x="1" y="3" width="14" height="10"/><path d="M1 3l7 6 7-6"/></svg>laura@zub.capital</p>
      </div>
    </div>
  </div>

  <address class="address">
    Zub Capital S.A<br>Harrowmere, Valdoria
  </address>
</section>

</body>
</html>
```